Pull Up Banner - Recruitment Company

We would like a design for a pull up banner.

For context: we are a recruitment business. We specialise in helping people in healthcare industry to find jobs in Australia.

I have come up with several ideas and text for the banner. Feel free to use the following as you see appropriate:

- Our logo (see attached)
- 'Healthcare Recruitment Agency'
- Some sort of imagine / cartoon of medical professionals (ie. doctor, nurse, physiotherapist, speech pathologist). A cartoon is more friendly than committing to a photo
- 'Empowering your next career move'
- 'Discover tailored opportunities based on your career preferences'
- Dot points (allied health, nursing, medical imaging)
- Contact info at the bottom including our website (www.quellastaffing.com.au, our Instagram handle @quellastaffing, Mobile: XXXX XXX XXX. The title section for contact information could be 'Get in touch:'

Feel free to submit a couple of designs and we can merge aspects that look good on your designs and find the perfect fit.
Thank you
Updates

Hello,

Thank you for your initial submissions to this project. I appreciate the time you've invested.

After reviewing the first attempt, I'd like to share some feedback and initial observations:

- Professionalism and engagement: Is the overall appearance of the banner professional? It's crucial that we have a high-quality design as this will represent our business.

- Image selection: The image (whether cartoon or real people) appears quite generic. Please consider submitting the banner with a few different photos in the middle for us to choose from. Ensure the image is a good fit and not simply a generic stock photo.

- Contact section: Kindly remove the phone number; we no longer wish to include it on the banner. Instead, please include our website (www.quellastaffing.com.au) and Instagram handle (@quellastaffing).

- Color scheme: White, black, and red/pink are preferred, or alternatively, blue. However, please avoid incorporating too many different colors as it may detract from the professional appearance.

We will be printing the design on a banner and require it to look professional and engaging.

Thank you once again for your submissions. I hope the feedback provided above is helpful.

Warm regards,

Target Market(s)

Allied Health Australia

Font styles to use
Serif

Colors
0054AA
0677BA
7BADD7
CADEEF
E8F1F8
0094D4
00A9DD
6FCCEA
C7EBF8
E9F6FB
EB3D1F
EC4F4E
F09395
F8D3D4
FCEDEE

```html
<!DOCTYPE html>
<html lang="en">
<head>
<meta charset="utf-8">
<title>Quella Staffing – Pull Up Banner</title>
<link rel="stylesheet" href="https://fonts.googleapis.com/css2?family=Anton&family=Poppins:wght@500;600;700&family=Montserrat:wght@500;600&display=swap">
<style>
  :root {
    --brand-blue: #1f2fc8;
    --ink: #0b0b0b;
    --paper: #ffffff;
    --band-dark: #1c1c1c;
    --stage: #e6e6e6;
    --illus-a: #c8d6ec;
    --illus-b: #8fc9c2;
  }
  * { box-sizing: border-box; margin: 0; padding: 0; }
  html, body { width: 1090px; height: 1200px; overflow: hidden; }
  body { background: var(--stage); position: relative; font-family: "Poppins", sans-serif; }

  .banner {
    position: absolute; left: 308px; top: 20px;
    width: 474px; height: 1160px;
    background: var(--paper);
    overflow: hidden;
  }
  .banner > * { position: absolute; }

  .brand {
    top: 58px; left: 0; width: 100%;
    text-align: center;
    font-family: "Montserrat", sans-serif; font-weight: 600;
    font-size: 30px; letter-spacing: 4px; color: var(--ink);
    line-height: 1;
  }
  .brand-sub {
    display: block; margin-top: 8px;
    font-size: 11px; letter-spacing: 3px;
  }

  .headline {
    top: 146px; left: 0; width: 100%;
    text-align: center;
    font-family: "Anton", sans-serif;
    font-size: 58px; line-height: 59px;
    text-transform: uppercase;
  }
  .headline .blue { color: var(--brand-blue); }
  .headline .black { color: var(--ink); }

  .dots {
    top: 324px; left: 50%; transform: translateX(-50%);
    display: flex; gap: 7px;
  }
  .dots span { width: 8px; height: 8px; border-radius: 50%; background: var(--ink); }

  .tagline {
    top: 342px; left: 0; width: 100%;
    text-align: center;
    font-weight: 600; font-size: 17.5px; color: var(--brand-blue);
  }

  .team-illustration {
    top: 419px; left: 39px; width: 396px; height: 248px;
    background: linear-gradient(90deg, var(--illus-a), var(--paper) 50%, var(--illus-b));
    border-radius: 6px;
  }

  .discover {
    top: 703px; left: 0; width: 100%;
    text-align: center;
    font-family: "Montserrat", sans-serif; font-weight: 600;
    font-size: 13px; letter-spacing: 2.6px; color: var(--ink);
  }
  .preferences {
    top: 718px; left: 0; width: 100%;
    text-align: center;
    font-family: "Anton", sans-serif; font-size: 34px; line-height: 40px;
    text-transform: uppercase;
  }
  .preferences .black { color: var(--ink); }
  .preferences .blue { color: var(--brand-blue); }

  .side-bar { top: 822px; width: 35px; height: 109px; background: var(--brand-blue); }
  .side-bar.left { left: 0; }
  .side-bar.right { right: 0; }

  .specialty {
    top: 822px; width: 110px; height: 109px;
    border: 2px solid var(--brand-blue);
    display: flex; align-items: center; justify-content: center;
    text-align: center;
    font-weight: 500; font-size: 21px; line-height: 1.2; color: var(--ink);
  }
  .specialty.allied { left: 55px; }
  .specialty.nursing { left: 185px; }
  .specialty.medical { left: 312px; }

  .contact-band {
    top: 944px; left: 0; width: 100%; height: 190px;
    background: var(--band-dark);
    text-align: center; color: var(--paper);
  }
  .contact-title {
    margin-top: 20px;
    font-family: "Anton", sans-serif; font-size: 35px; line-height: 40px;
    color: var(--brand-blue); text-transform: uppercase;
  }
  .contact-line {
    display: flex; align-items: center; justify-content: center; gap: 8px;
    font-weight: 600;
  }
  .contact-line.phone { margin-top: 8px; font-family: "Anton", sans-serif; font-size: 27px; font-weight: 400; }
  .contact-line.web { margin-top: 4px; font-size: 17px; }
  .contact-line.social { margin-top: 4px; font-size: 17px; }
  .contact-line svg { flex: none; }
</style>
</head>
<body>
  <main class="banner">
    <div class="brand">QUELLA<span class="brand-sub">STAFFING</span></div>

    <h1 class="headline">
      <span class="blue">Healthcare</span><br>
      <span class="black">Recruitment</span><br>
      <span class="blue">Agency</span>
    </h1>

    <div class="dots"><span></span><span></span><span></span><span></span><span></span></div>

    <p class="tagline">Empowering your next career move</p>

    <div class="team-illustration" role="img" aria-label="Cartoon group of five healthcare professionals: surgeon, doctors and nurses in scrubs and white coats"></div>

    <p class="discover">DISCOVER TAILORED OPPORTUNITIES</p>
    <h2 class="preferences">
      <span class="black">Based on your</span><br>
      <span class="blue">Career preferences</span>
    </h2>

    <div class="side-bar left"></div>
    <div class="specialty allied">Allied<br>health</div>
    <div class="specialty nursing">Nursing</div>
    <div class="specialty medical">Medical</div>
    <div class="side-bar right"></div>

    <section class="contact-band">
      <h3 class="contact-title">Get in touch</h3>
      <p class="contact-line phone">
        <svg width="26" height="26" viewBox="0 0 26 26" aria-hidden="true">
          <circle cx="13" cy="13" r="13" fill="var(--brand-blue)"/>
          <path d="M8.5 7.5c.8-.8 1.6-.6 2 .1l1.2 2c.3.6.1 1.1-.4 1.5l-.8.6c.6 1.5 1.9 2.9 3.4 3.6l.6-.8c.4-.5.9-.7 1.5-.4l2 1.2c.7.4.9 1.2.1 2l-.9.9c-.9.9-3.5.4-6.2-2.3S7.2 9.3 8.1 8.4z" fill="var(--band-dark)"/>
        </svg>
        9123 456 780
      </p>
      <p class="contact-line web">
        <svg width="20" height="20" viewBox="0 0 20 20" aria-hidden="true">
          <circle cx="10" cy="10" r="10" fill="var(--brand-blue)"/>
          <g fill="none" stroke="var(--band-dark)" stroke-width="1.2">
            <circle cx="10" cy="10" r="6"/>
            <ellipse cx="10" cy="10" rx="2.6" ry="6"/>
            <path d="M4 10h12M5 7h10M5 13h10"/>
          </g>
        </svg>
        www.quellastaffing.com.au
      </p>
      <p class="contact-line social">
        <svg width="18" height="18" viewBox="0 0 18 18" aria-hidden="true">
          <circle cx="9" cy="9" r="9" fill="var(--brand-blue)"/>
        </svg>
        @quellastaffing
      </p>
    </section>
  </main>
</body>
</html>
```